Coastline Premier Retreats Business Card Design

Design a business card for Coastline Premier Retreats. Look at the website for colors and reference. Card should have logo, name, title, office number, mobile number, email, URL and a tagline like, "Luxury Hotel & Resort Email Marketing" (This might change).

https://www.coastlinepremierretreats.example

The rest I will leave up to your imagination.

Contact Information for Business Card

Logo, name, title, office number, mobile number, email, URL and a tagline like, "Luxury Hotel & Resort Email Marketing" (This might change).

```html
<!DOCTYPE html>
<html lang="en">
<head>
<meta charset="utf-8">
<title>Coastline Premier Retreats – Business Card</title>
<link rel="stylesheet" href="https://fonts.googleapis.com/css2?family=Montserrat:wght@800&family=Arimo:wght@400;700&display=swap">
<style>
  :root {
    --orange: #f07322;
    --ink: #1a1a1a;
    --paper: #ffffff;
    --backdrop: #d9d9d9;
    --body-text: #222222;
  }
  * { box-sizing: border-box; margin: 0; padding: 0; }
  html, body { width: 1200px; height: 900px; overflow: hidden; }
  body {
    background: var(--backdrop);
    font-family: "Arimo", Arial, sans-serif;
    position: relative;
  }
  .card {
    position: absolute;
    left: 320px;
    width: 560px;
    height: 320px;
    border-radius: 22px;
    overflow: hidden;
    box-shadow: 0 6px 18px rgba(0,0,0,0.25);
  }
  .card-back { top: 90px; background: var(--orange); }
  .card-front { top: 470px; background: var(--paper); }

  .brand-name {
    font-family: "Montserrat", Arial, sans-serif;
    font-weight: 800;
    text-transform: uppercase;
    line-height: 1.05;
    display: flex;
    align-items: center;
    gap: 14px;
  }
  .brand-square { flex: none; background: currentColor; }

  .card-back .brand-name {
    position: absolute;
    inset: 0;
    justify-content: center;
    color: var(--paper);
    font-size: 34px;
  }
  .card-back .brand-square { width: 26px; height: 26px; }

  .card-front .brand-name {
    position: absolute;
    left: 34px; top: 82px;
    width: 230px;
    color: var(--ink);
    font-size: 21px;
  }
  .card-front .brand-square { width: 18px; height: 18px; background: var(--orange); }

  .divider {
    position: absolute;
    left: 278px; top: 34px;
    width: 2px; height: 160px;
    background: var(--orange);
  }
  .contact-block {
    position: absolute;
    left: 294px; top: 28px;
    width: 250px;
    color: var(--body-text);
    font-size: 12.5px;
    line-height: 1.32;
  }
  .person-name {
    color: var(--orange);
    font-weight: 700;
    font-size: 19px;
    letter-spacing: 0.3px;
    margin-bottom: 2px;
  }
  .person-role, .tagline { font-size: 13.5px; }
  .tagline { margin-bottom: 6px; }
  .contact-list { list-style: none; }
  .contact-list li { display: flex; align-items: center; gap: 7px; height: 19px; white-space: nowrap; }
  .contact-icon { width: 12px; height: 12px; flex: none; }

  .footer-band {
    position: absolute;
    left: 0; right: 0; bottom: 0;
    height: 70px;
    background: linear-gradient(180deg, var(--orange) 0, var(--orange) 8px, var(--ink) 8px, var(--ink) 100%);
  }
</style>
</head>
<body>

  <section class="card card-back" aria-label="Card back">
    <div class="brand-name"><span class="brand-square"></span><span>Coastline<br>Premier Retreats</span></div>
  </section>

  <section class="card card-front" aria-label="Card front">
    <div class="footer-band" role="img" aria-label="Decorative orange and black wave band along the bottom edge"></div>

    <div class="brand-name"><span class="brand-square"></span><span>Coastline<br>Premier<br>Retreats</span></div>

    <div class="divider"></div>

    <div class="contact-block">
      <p class="person-name">DANIEL MARSH</p>
      <p class="person-role">Co-Founder</p>
      <p class="tagline">Luxury Hotel &amp; Resort<br>Email Marketing</p>
      <ul class="contact-list">
        <li>
          <svg class="contact-icon" viewBox="0 0 12 12" aria-hidden="true"><path d="M2.5 1 L4.5 1 L5.2 3.5 L4 4.5 C4.6 5.8 6.2 7.4 7.5 8 L8.5 6.8 L11 7.5 L11 9.5 C11 10.3 10.3 11 9.5 11 C5 11 1 7 1 2.5 C1 1.7 1.7 1 2.5 1 Z" fill="var(--orange)"/></svg>
          <span>555-201-4418</span>
        </li>
        <li>
          <svg class="contact-icon" viewBox="0 0 12 12" aria-hidden="true"><rect x="3" y="0.8" width="6" height="10.4" rx="1.2" fill="none" stroke="var(--orange)" stroke-width="1.3"/><circle cx="6" cy="9.3" r="0.7" fill="var(--orange)"/></svg>
          <span>555-307-6621</span>
        </li>
        <li>
          <svg class="contact-icon" viewBox="0 0 12 12" aria-hidden="true"><rect x="0.5" y="2.5" width="11" height="7.5" fill="var(--orange)"/><path d="M0.8 2.8 L6 6.8 L11.2 2.8" fill="none" stroke="var(--paper)" stroke-width="1"/></svg>
          <span>info@coastlinepremierretreats.example</span>
        </li>
        <li>
          <svg class="contact-icon" viewBox="0 0 12 12" aria-hidden="true"><circle cx="6" cy="6" r="5.3" fill="none" stroke="var(--orange)" stroke-width="1.2"/><ellipse cx="6" cy="6" rx="2.3" ry="5.3" fill="none" stroke="var(--orange)" stroke-width="1"/><path d="M0.8 6 H11.2" stroke="var(--orange)" stroke-width="1"/></svg>
          <span>www.coastlinepremierretreats.example</span>
        </li>
      </ul>
    </div>
  </section>

</body>
</html>
```